Small legal and financial translation company needs Squarespace website, brochure and logo

Hello,
We are Lumarin Services (www.lumarinservices-example.com), a boutique legal and financial translation company. We offer our services mainly to Spanish customers. Our primary line of business is the translation of financial statements, but we translate a wide variety legal and financial texts.
The project we are offering comprises three parts: a redo of the current website, an informational brochure for potential customer and a logo design. These three parts should provide a consistent image. We would develop content soon.
We are looking for a website that would look like a typical law firm website, nothing too fancy. Right now, it is in English, Spanish and French, although the new site need only be in English and Spanish. There must be good toggling between the English and Spanish versions. There would be no need for tie-ins to social media and it would not contain a blog. Basically, a static site. We aren't interesting in driving traffic to the site or SEO, as we will contact nearly all potential customers beforehand. The website must be built in Squarespace to enable a smooth transition. The content would be similar to the current page, we'll be working on the exact content, but a rough draft is attached.
The brochure will be some three pages and would introduce the company to potential customers, using similar images as the website and the logo to be designed.
The only specifications for the logo is, as the website and brochure, it convey a sense of security and trust.
Feel free to ask with any questions as this is the first time we have used this platform.
Thank you!
Updates

I've added a more or less final version for the text in the brochure and updated the brief. Added Wednesday, June 10, 2015

Target Market(s)

Spanish law firms, auditors, accountants, banks, investment firms

Industry/Entity Type

Finance

Logo Text

Lumarin Services

Number of Pages Required

5+ page

Font styles to use
Serif

Requirements
Must have
• The website must be built in Squarespace and have a good option to toggle between English and Spanish versions.
• Brochure must be in both English and Spanish, I'm attaching a rough draft of the information that it will probably have. This should give an idea about what to include and the spacing. I will update it to include the final information.
Nice to have
• Would be nice to have some quality finance- and legal-related images
Should not have
• Vibrant colours

```html
<!DOCTYPE html>
<html lang="en">
<head>
<meta charset="utf-8">
<title>Lumarin Services – Legal and Financial Translation</title>
<link href="https://fonts.googleapis.com/css2?family=Cinzel:wght@400;700&family=Marcellus&family=Lato:wght@300;400&family=Open+Sans:wght@400;600;700&display=swap" rel="stylesheet">
<style>
:root{
  --navy:#2b3f8a;
  --heading-blue:#2f4391;
  --black:#000;
  --ink:#111;
  --white:#fff;
  --grey-band:#e4e4e4;
  --rule:#d8d8d8;
  --muted:#b5b5b5;
  --link-blue:#4a90e2;
}
*{margin:0;padding:0;box-sizing:border-box}
html,body{width:1200px;height:2289px;overflow:hidden;background:var(--white)}
body{position:relative;font-family:"Open Sans",Arial,sans-serif;color:var(--ink)}
h1,h2,h3,h4,h5{font-weight:400}
.abs{position:absolute}

/* top bar */
.top-bar{left:0;top:0;width:1200px;height:29px;background:var(--black)}
.lang-select{right:81px;top:6px;color:var(--white);font-size:10px;display:flex;align-items:center;gap:6px}
.lang-select span.box{border:1px solid var(--white);padding:0 16px 0 3px;position:relative;line-height:14px}
.lang-select span.box::after{content:"";position:absolute;right:4px;top:5px;border:3px solid transparent;border-top-color:var(--white)}

/* header */
.site-header{left:0;top:29px;width:1200px;height:99px;background:var(--white);border-bottom:1px solid #c9a6ad}
.brand{left:101px;top:32px;display:flex;align-items:center;gap:12px}
.brand-mark{width:46px;height:46px;background:var(--navy)}
.brand-name{font-family:"Cinzel",Georgia,serif;font-size:33px;color:var(--ink);letter-spacing:1px}
.main-nav{right:98px;top:42px;display:flex;gap:40px;font-family:"Marcellus",Georgia,serif;font-size:17px;color:var(--ink)}

/* hero */
.hero-photo{left:0;top:128px;width:1200px;height:450px;background:linear-gradient(100deg,#4a4a4a 0%,#8c8c8c 25%,#d6d6d6 55%,#f0f0f0 80%,#dcdcdc 100%)}
.hero-band{left:0;top:280px;width:687px;height:82px;background:rgba(255,255,255,.72)}
.hero-title{left:104px;top:301px;font-family:"Lato",Arial,sans-serif;font-weight:300;font-size:32px;color:var(--navy);letter-spacing:.5px}
.service-band{left:0;top:578px;width:1200px;height:248px;background:var(--grey-band)}

.service-card{top:546px;width:467px;height:229px;background:var(--black);color:var(--white);text-align:center;box-shadow:0 28px 30px -18px rgba(0,0,0,.55)}
.service-card h3{margin-top:80px;font-family:"Cinzel",Georgia,serif;font-size:20px;letter-spacing:1.5px}
.service-card p{margin:6px auto 0;width:400px;font-size:14px;line-height:18px}
.btn-more{display:inline-block;width:97px;height:30px;border-radius:5px;font-size:14px;line-height:27px;text-align:center}
.service-card .btn-more{margin-top:14px;border:1.5px solid var(--white);color:var(--white)}
.card-icon{top:488px;width:115px;height:115px;border-radius:50%;background:var(--navy);border:5px solid var(--white);display:flex;align-items:center;justify-content:center}

/* about */
.intro-col{top:893px;width:449px}
.intro-col h2{font-family:"Cinzel",Georgia,serif;font-size:28px;color:var(--heading-blue);letter-spacing:1px}
.intro-col p{margin-top:14px;font-size:13.5px;line-height:23px;text-align:justify}
.intro-col .btn-more{position:absolute;top:250px;left:0;border:2px solid var(--ink);color:var(--ink)}

/* why choose */
.why-section{left:0;top:1240px;width:1200px;height:448px;background:linear-gradient(160deg,#3a3a3a 0%,#151515 35%,#222 60%,#0d0d0d 100%)}
.why-title{left:0;top:1286px;width:1200px;text-align:center;font-family:"Cinzel",Georgia,serif;font-size:28px;color:var(--white);letter-spacing:1.5px}
.why-rule-v{width:1px;background:rgba(255,255,255,.12)}
.why-rule-h{height:1px;background:rgba(255,255,255,.12)}
.feature{width:300px;display:flex;gap:16px}
.feature-icon{flex:none;width:61px;height:61px;border:2px solid var(--white);border-radius:50%;display:flex;align-items:center;justify-content:center}
.feature h4{margin-top:8px;font-family:"Marcellus",Georgia,serif;font-size:18px;color:var(--white)}
.feature p{margin-top:5px;font-size:12.5px;line-height:18px;color:var(--muted)}

/* clients */
.clients-title{left:0;top:1766px;width:1200px;text-align:center;font-family:"Cinzel",Georgia,serif;font-size:28px;color:var(--heading-blue);letter-spacing:1.5px}
.client-row{left:101px;top:1847px;width:998px;height:103px;display:flex;border:1px solid var(--rule)}
.client-slot{flex:1;border-right:1px solid var(--rule);display:flex;align-items:center;justify-content:center;gap:8px;font-size:15px;font-weight:700;color:#222}
.client-slot:last-child{border-right:0}
.client-dot{width:12px;height:12px;border-radius:50%;background:#222}

/* footer */
.site-footer{left:0;top:2003px;width:1200px;height:286px;background:var(--black);color:var(--white)}
.footer-col{top:2033px;width:235px}
.footer-col h5{font-size:15px;font-weight:700;margin-bottom:15px}
.footer-col h5.light{font-weight:400}
.footer-col ul{list-style:none}
.footer-col li{font-size:13.5px;line-height:31px;padding-left:15px;position:relative}
.footer-col li::before{content:"";position:absolute;left:0;top:14px;width:4px;height:4px;border-radius:50%;background:var(--white)}
.contact-line{font-size:13.5px;line-height:20px;margin-bottom:11px}
.contact-line a{color:var(--link-blue);text-decoration:none}
.map-area{left:851px;top:2081px;width:250px;height:140px;background:linear-gradient(135deg,#d9d6cf,#c8c5bd 60%,#d4d1ca)}
</style>
</head>
<body>

<div class="abs top-bar"></div>
<div class="abs lang-select">Select Language: <span class="box">English</span></div>

<header class="abs site-header">
  <div class="abs brand"><div class="brand-mark"></div><div class="brand-name">Lumarin Services</div></div>
  <nav class="abs main-nav"><span>Home</span><span>About Us</span><span>Services</span><span>FAQ's</span><span>Contact Us</span></nav>
</header>

<div class="abs hero-photo" role="img" aria-label="Black and white photo of a hand signing a document with a pen beside a keyboard and coffee cup"></div>
<div class="abs hero-band"></div>
<h1 class="abs hero-title">HIGH-QUALITY TRANSLATION SERVICES</h1>

<div class="abs service-band"></div>
<section class="abs service-card" style="left:113px">
  <h3>Legal Translation</h3>
  <p>Lorem ipsum dolor sit amet, consectetuer adipiscing elit, sed diam nonummy nibh euismod tincidunt ut.</p>
  <span class="btn-more">More</span>
</section>
<section class="abs service-card" style="left:618px">
  <h3>Financial Translation</h3>
  <p>Lorem ipsum dolor sit amet, consectetuer adipiscing elit, sed diam nonummy nibh euismod tincidunt ut.</p>
  <span class="btn-more">More</span>
</section>
<div class="abs card-icon" style="left:289px">
  <svg width="56" height="56" viewBox="0 0 56 56" fill="#fff"><rect x="10" y="12" width="22" height="12" rx="2" transform="rotate(-40 21 18)"/><rect x="20" y="22" width="26" height="5" transform="rotate(40 20 22)"/><rect x="6" y="42" width="24" height="5" rx="1"/></svg>
</div>
<div class="abs card-icon" style="left:794px">
  <svg width="52" height="52" viewBox="0 0 52 52" fill="none" stroke="#fff" stroke-width="3"><rect x="6" y="6" width="40" height="38" rx="3"/><circle cx="26" cy="25" r="8"/><path d="M12 46v3M40 46v3"/></svg>
</div>

<section class="abs intro-col" style="left:118px">
  <h2>Who Are We?</h2>
  <p>We are a small, highly professional and qualified group of professionals with backgrounds in law, financial services and translation and interpretation that boasts experience in global consulting and auditing firms, law firms and companies from a cross section of industries. Sensitive to the workings of the financial world, we are detail-oriented experts striving to facilitate understanding among investors, companies and international organisations.</p>
  <span class="btn-more">More</span>
</section>
<section class="abs intro-col" style="left:630px">
  <h2>What We Do?</h2>
  <p>We provide high-quality translation services in English, Spanish and French for legal and financial documents, particularly for your company's financial statements and annual reports. The translation tools we have fashioned over the years ensure that your investors and other parties recognise your company's worth and dedication while reflecting the distinction between financial statements prepared under IFRSs or local GAAP.</p>
  <span class="btn-more">More</span>
</section>

<div class="abs why-section" role="img" aria-label="Dark black and white photo of modern office towers seen from below"></div>
<h2 class="abs why-title">Why Choose Us?</h2>
<div class="abs why-rule-v" style="left:412px;top:1340px;height:340px"></div>
<div class="abs why-rule-v" style="left:761px;top:1340px;height:340px"></div>
<div class="abs why-rule-h" style="left:75px;top:1497px;width:1070px"></div>

<div class="abs feature" style="left:99px;top:1358px">
  <div class="feature-icon"><svg width="30" height="30" viewBox="0 0 30 30" fill="#fff"><ellipse cx="15" cy="16" rx="12" ry="9"/><rect x="8" y="22" width="4" height="5"/><rect x="18" y="22" width="4" height="5"/></svg></div>
  <div><h4>Save Money</h4><p>Lorem ipsum dolor sit amet, consectetuer adipiscing elit, sed diam nonummy nibh euismod.</p></div>
</div>
<div class="abs feature" style="left:443px;top:1358px">
  <div class="feature-icon"><svg width="30" height="30" viewBox="0 0 30 30" fill="#fff"><path d="M15 3l3.6 7.6 8.3 1-6.1 5.7 1.6 8.2L15 21.4l-7.4 4.1 1.6-8.2-6.1-5.7 8.3-1z"/></svg></div>
  <div><h4>Quality Guaranteed</h4><p>Lorem ipsum dolor sit amet, consectetuer adipiscing elit, sed diam nonummy nibh euismod.</p></div>
</div>
<div class="abs feature" style="left:784px;top:1358px">
  <div class="feature-icon"><svg width="30" height="30" viewBox="0 0 30 30" fill="#fff"><circle cx="12" cy="12" r="5"/><path d="M3 27c0-6 4-9 9-9s9 3 9 9z"/><circle cx="23" cy="7" r="4" fill="none" stroke="#fff" stroke-width="2"/></svg></div>
  <div><h4>Native Translators Only</h4><p>Lorem ipsum dolor sit amet, consectetuer adipiscing elit, sed diam nonummy nibh euismod.</p></div>
</div>
<div class="abs feature" style="left:99px;top:1523px">
  <div class="feature-icon"><svg width="30" height="30" viewBox="0 0 30 30" fill="none" stroke="#fff" stroke-width="3"><circle cx="15" cy="15" r="11"/><path d="M15 8v7h6"/></svg></div>
  <div><h4>Consistency Over Time</h4><p>Lorem ipsum dolor sit amet, consectetuer adipiscing elit, sed diam nonummy nibh euismod.</p></div>
</div>
<div class="abs feature" style="left:443px;top:1523px">
  <div class="feature-icon"><svg width="30" height="30" viewBox="0 0 30 30" fill="none" stroke="#fff" stroke-width="2.5"><rect x="6" y="6" width="18" height="13" rx="1"/><path d="M3 23h24"/></svg></div>
  <div><h4>Use of Technology</h4><p>Lorem ipsum dolor sit amet, consectetuer adipiscing elit, sed diam nonummy nibh euismod.</p></div>
</div>
<div class="abs feature" style="left:784px;top:1523px">
  <div class="feature-icon"><svg width="32" height="30" viewBox="0 0 32 30" fill="#fff"><circle cx="16" cy="10" r="4.5"/><circle cx="7" cy="12" r="3.5"/><circle cx="25" cy="12" r="3.5"/><path d="M9 25c0-5 3-8 7-8s7 3 7 8z"/><path d="M1 24c0-4 2-6 6-6 1.5 0 2.5.3 3.3.8C8.5 20 7.6 22 7.5 24zM31 24c0-4-2-6-6-6-1.5 0-2.5.3-3.3.8 1.8 1.2 2.7 3.2 2.8 5.2z"/></svg></div>
  <div><h4>Years of Experience</h4><p>Lorem ipsum dolor sit amet, consectetuer adipiscing elit, sed diam nonummy nibh euismod.</p></div>
</div>

<h2 class="abs clients-title">Our Clients</h2>
<div class="abs client-row">
  <div class="client-slot"><span class="client-dot"></span>Calder &amp; Vey</div>
  <div class="client-slot"><span class="client-dot"></span>Northmark</div>
  <div class="client-slot"><span class="client-dot"></span>Ostera Bank</div>
  <div class="client-slot"><span class="client-dot"></span>Halden Audit</div>
  <div class="client-slot"><span class="client-dot"></span>Verano Capital</div>
</div>

<footer class="abs site-footer"></footer>
<div class="abs footer-col" style="left:101px;color:#fff">
  <h5>Quick Links</h5>
  <ul><li>Home</li><li>About Us</li><li>FAQ's</li><li>Our Clients</li><li>Privacy Policy</li></ul>
</div>
<div class="abs footer-col" style="left:351px;color:#fff">
  <h5 class="light">Services We Offer</h5>
  <ul><li>Legal Translation</li><li>Financial Translation</li><li>Document Translation</li><li>Interpreting</li><li>Service Levels</li></ul>
</div>
<div class="abs footer-col" style="left:601px;color:#fff">
  <h5>Contact Info</h5>
  <p class="contact-line">Address: 118 Harbor Lane<br>Fairview, AL(Alabama) 36000</p>
  <p class="contact-line">Phone: (555) 014-2770</p>
  <p class="contact-line">Fax: &nbsp;(555) 014-2771</p>
  <p class="contact-line">Mail:<br><a>info@lumarinservices-example.com</a></p>
</div>
<div class="abs footer-col" style="left:851px;color:#fff">
  <h5>Find Us on Map</h5>
</div>
<div class="abs map-area" role="img" aria-label="Street map showing the office location"></div>

</body>
</html>
```